real esate business card with company logo and name

we need a business card design for a real esate company

The company name is Walsh & Brand Pty Ltd, and we have our logo designed and will upload. We want classic or moden feel. Black or white background. looks more textured. Should include folowinginformations
Owen Walsh and Lucy Brand
Sales Agents & Onsite Manager
p: 07 5948 2063
F: 07 5948 2174
M:0431 857 219
3/42 Marlow Crescent, FERNLEA QLD 4213

We want this business card looks professonal. Thank you in advance.

Industry/Entity Type

Real Estate Agent

Contact Information for Business Card

Owen Walsh and Lucy Brand
Onsite Manager & Sales Agents
p: 07 5948 2063
M:0431 857 219

Font styles to use
Serif

Colors
000000
fbfbfb
333333
959595

Requirements
Must have
• company logo and name, black or white back ground

```html
<!DOCTYPE html>
<html lang="en">
<head>
<meta charset="utf-8">
<title>Walsh &amp; Brand Pty Ltd – Business Card</title>
<link rel="stylesheet" href="https://fonts.googleapis.com/css2?family=Lato:wght@400;700&family=Oswald:wght@400&display=swap">
<style>
  :root {
    --backdrop: #2b2b2b;
    --card: #000000;
    --band: #d0d0d2;
    --ink-light: #fbfbfb;
    --ink-muted: #bdbdbd;
    --ink-dark: #111111;
    --mark-grey: #959595;
    --mark-dark: #333333;
  }
  * { margin: 0; padding: 0; box-sizing: border-box; }
  html, body {
    width: 1200px; height: 1086px; overflow: hidden;
    background: var(--backdrop);
  }
  .card {
    position: absolute; left: 254px; width: 677px; height: 387px;
    background: var(--card); overflow: hidden;
  }
  .card--front { top: 126px; }
  .card--back { top: 586px; }

  .name-marker {
    position: absolute; left: 0; top: 48px; width: 14px; height: 48px;
    background: var(--band);
  }
  .agent {
    position: absolute; left: 43px; top: 44px;
    font-family: "Lato", sans-serif; color: var(--ink-light);
  }
  .agent__name { font-weight: 700; font-size: 28px; line-height: 1.05; }
  .agent__role { font-weight: 400; font-size: 19px; color: #d8d8d8; margin-top: 2px; }

  .company {
    font-family: "Oswald", sans-serif; font-weight: 400;
    text-transform: uppercase; color: var(--ink-muted);
    letter-spacing: 0.5px; white-space: nowrap;
  }
  .company--front { position: absolute; right: 38px; top: 38px; font-size: 23px; }

  .contact-band {
    position: absolute; left: 0; top: 222px; width: 610px; height: 143px;
    background: var(--band);
    font-family: "Lato", sans-serif; color: var(--ink-dark);
    padding: 6px 0 0 38px;
  }
  .contact-list { list-style: none; }
  .contact-list li {
    display: flex; align-items: center; gap: 6px;
    font-size: 21px; line-height: 26px;
  }
  .contact-list svg { width: 16px; height: 16px; flex: none; }
  .address { margin-top: 7px; font-size: 18px; line-height: 23px; }

  .brand-square {
    position: absolute; right: 14px; top: 252px; width: 72px; height: 72px;
    background: var(--mark-grey);
  }

  .back-square {
    position: absolute; left: 258px; top: 64px; width: 160px; height: 160px;
    background: linear-gradient(160deg, var(--mark-grey), var(--mark-dark));
  }
  .company--back {
    position: absolute; left: 0; right: 0; top: 278px;
    text-align: center; font-size: 33px; color: #a8a8a8;
  }
</style>
</head>
<body>

<section class="card card--front" aria-label="Business card front">
  <div class="name-marker"></div>
  <div class="agent">
    <p class="agent__name">Owen Walsh</p>
    <p class="agent__role">Sales Agents</p>
  </div>
  <p class="company company--front">Walsh &amp; Brand Pty Ltd.</p>

  <div class="contact-band">
    <ul class="contact-list">
      <li>
        <svg viewBox="0 0 16 16" aria-hidden="true"><rect x="4" y="1" width="8" height="14" rx="1.5" fill="none" stroke="#111" stroke-width="1.6"/><rect x="7" y="12" width="2" height="1.2" fill="#111"/></svg>
        0431 857 219
      </li>
      <li>
        <svg viewBox="0 0 16 16" aria-hidden="true"><path d="M1 6c0-2 3-3 7-3s7 1 7 3v1h-3.5V5.5h-7V7H1z" fill="#111"/><path d="M3.5 8h9l1.5 6H2z" fill="#111"/><circle cx="8" cy="11" r="1.5" fill="#d0d0d2"/></svg>
        07 5948 2063
      </li>
      <li>
        <svg viewBox="0 0 16 16" aria-hidden="true"><rect x="4" y="2" width="8" height="4" fill="#111"/><rect x="1" y="6" width="14" height="6" rx="1" fill="#111"/><rect x="4" y="10" width="8" height="4" fill="#111" stroke="#d0d0d2" stroke-width="1"/></svg>
        07 5948 2174
      </li>
    </ul>
    <p class="address">3/42 Marlow Crescent<br>FERNLEA QLD 4213</p>
  </div>
  <div class="brand-square"></div>
</section>

<section class="card card--back" aria-label="Business card back">
  <div class="back-square"></div>
  <p class="company company--back">Walsh &amp; Brand Pty Ltd.</p>
</section>

</body>
</html>
```